Basic / Quick Business Card

Quick easy design project!

Need a one sided basic business card that matches font & style of brand and bottle label for our gourmet condiment, Brindle Harrow Sauce. Brindle Harrow Sauce is sold in specialty retail, gourmet groceries and appears on chef-driven restaurant menus, so the target market is a high end, gourmet, artisan-made food-loving customer.

Files Included:
Sauce Bottle Label
Brindle Harrow Sauce Round Logos

**About the logos - the logo may be used in a circle or alone vertically as on side of the bottle label**

Layout of Card:
May be vertical or horizontal based on designer ideas.

Logo usage (in circle vs. stand alone vertical logo) is up to designers descretion as well.

Reverse side of business card will be various high end / professional product photos / food shots using us.kelbo.com system. **Designer on this project will NOT design a reserve for the card.**

Paper that will be used for printing:
Kelbo Standard - it's a WHITE paper, but we use a cream background on Brindle Harrow Sauce branding, so please take this into account on design to stay brand consistent.

Elements & Copy for Card:
1. Logo in either script horizontal or vertical version
2. Copy: "Artisan Made - Small Batch"
3. Name - Wes Dorrance
4. Title - Creator
5. Phone - xxx.xxx.xxxx
6. xxxx@brindleharrow.com
7. URL: brindleharrowsauce.com
8. Social Media: @getbrindleharrow on Quillo / Pagora / Lumigrid

Please provide final files in Illustrator or InDesign format.

```html
<!DOCTYPE html>
<html lang="en">
<head>
<meta charset="utf-8">
<title>Brindle Harrow Sauce – Business Card</title>
<link rel="stylesheet" href="https://fonts.googleapis.com/css2?family=Kurale&display=swap">
<style>
  :root {
    --backdrop: #d9d6d0;
    --card-dark: #2a2725;
    --cream: #eef0dc;
    --gold: #f0b21b;
    --ink: #2b2622;
    --white: #ffffff;
  }
  * { box-sizing: border-box; margin: 0; padding: 0; }
  html, body {
    width: 1200px; height: 833px; overflow: hidden;
    background: var(--backdrop);
  }
  .canvas {
    position: relative; width: 1200px; height: 833px;
    font-family: "Kurale", Georgia, serif;
    color: var(--ink);
  }
  .card {
    position: absolute; left: 75px; top: 116px;
    width: 1050px; height: 600px;
    background: var(--card-dark);
    box-shadow: 0 6px 18px rgba(0,0,0,.25);
  }
  .brand-mark {
    position: absolute; left: 110px; top: 150px;
    width: 300px; height: 300px;
    border: 9px solid var(--gold);
    border-radius: 50%;
    display: flex; align-items: center; justify-content: center;
    text-align: center;
  }
  .brand-name {
    color: var(--gold);
    font-size: 46px; line-height: 1.02;
  }
  .info-panel {
    position: absolute; left: 570px; top: 24px;
    width: 456px; height: 552px;
    background: var(--cream);
    padding: 56px 26px 0 32px;
  }
  .contact-list { list-style: none; }
  .contact-list li {
    display: flex; align-items: center; gap: 10px;
    font-size: 23px; line-height: 40px;
  }
  .contact-list svg { width: 20px; height: 20px; flex: none; }
  .divider {
    border: 0; border-top: 4px dotted var(--gold);
    margin: 16px 0 22px;
  }
  .social {
    display: flex; align-items: center; gap: 14px;
    font-size: 23px; margin-bottom: 4px;
  }
  .social-handle {
    display: inline-flex; align-items: center; gap: 5px;
    font-size: 18px;
  }
  .social-handle::before {
    content: ""; width: 12px; height: 12px; border-radius: 50%;
    background: var(--gold);
  }
  .tagline { font-size: 29px; line-height: 1.05; margin-top: 30px; }
  .name-band {
    position: absolute; left: 12px; right: 12px; bottom: 16px;
    height: 82px; background: var(--gold);
    display: flex; align-items: center; justify-content: center;
    color: var(--white); font-size: 35px;
  }
</style>
</head>
<body>
<div class="canvas">
  <div class="card">
    <div class="brand-mark">
      <span class="brand-name">Brindle<br>Harrow<br>Sauce</span>
    </div>
    <div class="info-panel">
      <ul class="contact-list">
        <li>
          <svg viewBox="0 0 20 20" aria-hidden="true"><circle cx="10" cy="10" r="8.5" fill="none" stroke="#2b2622" stroke-width="2"/><path d="M7 5.5l2 2-1.2 1.5c.6 1.3 1.5 2.2 2.8 2.8l1.5-1.2 2 2-1.4 1.6C9.5 14.3 5.7 10.5 5.4 7z" fill="#2b2622"/></svg>
          555-014-2736
        </li>
        <li>
          <svg viewBox="0 0 20 20" aria-hidden="true"><rect x="2" y="5" width="16" height="11" rx="1.5" fill="#2b2622"/><path d="M2.5 6l7.5 5.5L17.5 6" fill="none" stroke="#eef0dc" stroke-width="1.5"/></svg>
          wdorrance@brindleharrow.com
        </li>
        <li>
          <svg viewBox="0 0 20 20" aria-hidden="true"><g fill="none" stroke="#2b2622" stroke-width="1.6"><circle cx="10" cy="10" r="8"/><ellipse cx="10" cy="10" rx="3.5" ry="8"/><path d="M2 10h16M3.5 6h13M3.5 14h13"/></g></svg>
          www.brindleharrowsauce.com
        </li>
      </ul>
      <hr class="divider">
      <div class="social">
        <span>Follow Us On</span>
        <span class="social-handle">Pagora</span>
        <span class="social-handle">Quillo</span>
        <span class="social-handle">Lumigrid</span>
      </div>
      <hr class="divider">
      <p class="tagline">Artisan Made - Small Batch<br>sweet &amp; spicy</p>
      <div class="name-band">Wes Dorrance, Creator</div>
    </div>
  </div>
</div>
</body>
</html>
```